Powerpoint design template for LUMOTEX for new digital platform

We would like to use a PowerPoint template, we would like to create a new page, we would like to create a new digital platform LUMOTEX for schools and parents for the creation of playful communication and educational tools for children to enhance their positive development, amaze them learn in a playful way. This platform is going to be the most creative, stimulating and innovative classroom, easy to use and fast to implement. Scrapbooking, collages ... Magazine, newsletters Diplomla / awards Slideshows Facebook Calendars Organizers Greetings Games ... This powerpoint template will be used essential to We are looking for a professional design, positioning our brand in the children market with an adult hearing. so you will need to find a good deal. Primary target: nurseries & schools from 0 to 18 years old and universities (in 2nd phase) Secondary target: small & medium businesses Third target: general public, and TPE If it is a color scheme, then it is suggested that it be marketed in Europe (UK, Italy, Spain) and in a 2nd Stage USA and other countries. multiple options for front page, insidious pages (multiple styles with limited text and extended text) and final contact page We need something to read, we can not do it too much, but we can not do it. , and inside pages aligned to our logo

Target Market(s)

Target 1; Education with teacher Target 2; parents and grandparents

Industry/Entity Type

Education

Font styles to use
Other font styles liked:
• not decided. but not too fancy

Requirements
Must have
• Multi page options for front page, page insides (multiple styles with limited text and extended text) and final page contact
Nice to have
• do not have a lot of ideas. We need something to read, we can not get away from it
Should not have
• not too fancy and busy: keep clarity & simplicity while reassuring on quality

```html
<!DOCTYPE html>
<html lang="en">
<head>
<meta charset="utf-8">
<title>LUMOTEX – Content Page</title>
<link href="https://fonts.googleapis.com/css2?family=Roboto+Condensed:wght@400;700&display=swap" rel="stylesheet">
<style>
  :root {
    --lime: #d9e13f;
    --lime-deep: #b9cc2e;
    --lime-dark: #9fbf2a;
    --ink: #2b2b2b;
    --body-grey: #7a7a7a;
    --blue: #1aa9df;
    --pink: #e6338a;
    --orange: #f7941d;
    --white: #ffffff;
  }
  * { margin: 0; padding: 0; box-sizing: border-box; }
  html, body { width: 1200px; height: 900px; overflow: hidden; background: var(--white); }
  body { font-family: "Roboto Condensed", "Arial Narrow", sans-serif; }
  .slide { position: relative; width: 1200px; height: 900px; overflow: hidden; background: var(--white); }

  .header-band, .footer-band { position: absolute; left: 0; }
  .header-band { top: 0; width: 1200px; height: 120px; }
  .footer-band { bottom: 0; width: 1200px; height: 72px; }

  .project-title {
    position: absolute; left: 30px; top: 30px;
    font-size: 46px; font-weight: 700; color: var(--ink); letter-spacing: 0.2px;
  }

  .brand {
    position: absolute; left: 996px; top: 34px; width: 180px;
    display: flex; flex-direction: column; align-items: flex-start;
  }
  .brand-row { display: flex; align-items: center; gap: 8px; }
  .brand-mark { width: 16px; height: 16px; background: var(--pink); }
  .brand-name { font-size: 34px; font-weight: 700; color: var(--ink); line-height: 1; }
  .brand-tagline { font-size: 10px; font-weight: 400; color: var(--ink); letter-spacing: 1.5px; margin-top: 6px; line-height: 1.2; }

  .sections { position: absolute; left: 30px; top: 166px; width: 1080px; }
  .section { position: relative; padding-left: 82px; height: 196px; }
  .section-icon {
    position: absolute; left: 2px; top: 2px; width: 62px; height: 52px;
    border-radius: 4px;
  }
  .section--blue .section-icon { background: linear-gradient(135deg, #5cc4ea, var(--blue)); }
  .section--pink .section-icon { background: linear-gradient(135deg, #ef6aa8, var(--pink)); }
  .section--orange .section-icon { background: linear-gradient(135deg, #fab25a, var(--orange)); }

  .section-title { font-size: 31px; font-weight: 700; line-height: 1; margin-top: 14px; }
  .section--blue .section-title { color: var(--blue); }
  .section--pink .section-title { color: var(--pink); }
  .section--orange .section-title { color: var(--orange); }

  .section-body {
    margin-top: 12px; width: 990px;
    font-size: 22.5px; line-height: 36px; color: var(--body-grey); font-weight: 400;
  }

  .footer-url { position: absolute; left: 22px; bottom: 18px; font-size: 24px; color: var(--ink); }
  .page-number { position: absolute; right: 30px; bottom: 24px; font-size: 22px; color: var(--ink); }
</style>
</head>
<body>
<main class="slide">
  <svg class="header-band" viewBox="0 0 1200 120" aria-hidden="true">
    <polygon points="0,0 960,0 900,110 0,110" fill="var(--lime)"/>
    <polygon points="940,0 975,0 918,104 900,110" fill="var(--lime-deep)"/>
    <polygon points="960,0 990,0 936,98 918,104" fill="var(--lime-dark)"/>
    <polygon points="990,12 1140,0 1190,60 1100,120 980,60" fill="var(--lime)"/>
    <polygon points="985,20 1135,6 1182,60 1098,112 975,62" fill="var(--white)"/>
  </svg>

  <h1 class="project-title">PROJECT TITLE HERE</h1>

  <div class="brand">
    <div class="brand-row">
      <span class="brand-mark"></span>
      <span class="brand-name">LUMOTEX</span>
    </div>
    <span class="brand-tagline">YOUR TAGLINE<br>GOES HERE</span>
  </div>

  <section class="sections">
    <article class="section section--blue">
      <div class="section-icon" role="img" aria-label="Blue star wand icon"></div>
      <h2 class="section-title">SUBTEXT HERE</h2>
      <p class="section-body">Toffee caramels candy canes bonbon bonbon soufflé bonbon wafer. Topping I love halvah I love. Jujubes lemon drops I love jelly pie chocolate bar. Biscuit oat cake carrot cake. Muffin jelly beans chocolate choco-late. Sugar plum I love cheesecake marshmallow oreo cake sweet cookies topping jelly gummies.</p>
    </article>
    <article class="section section--pink">
      <div class="section-icon" role="img" aria-label="Pink star wand icon"></div>
      <h2 class="section-title">SUBTEXT HERE</h2>
      <p class="section-body">Toffee caramels candy canes bonbon bonbon soufflé bonbon wafer. Topping I love halvah I love. Jujubes lemon drops I love jelly pie chocolate bar. Biscuit oat cake carrot cake. Muffin jelly beans chocolate choco-late. Sugar plum I love cheesecake marshmallow oreo cake sweet cookies topping jelly gummies.</p>
    </article>
    <article class="section section--orange">
      <div class="section-icon" role="img" aria-label="Orange star wand icon"></div>
      <h2 class="section-title">SUBTEXT HERE</h2>
      <p class="section-body">Toffee caramels candy canes bonbon bonbon soufflé bonbon wafer. Topping I love halvah I love. Jujubes lemon drops I love jelly pie chocolate bar. Biscuit oat cake carrot cake. Muffin jelly beans chocolate choco-late. Sugar plum I love cheesecake marshmallow oreo cake sweet cookies topping jelly gummies.</p>
    </article>
  </section>

  <svg class="footer-band" viewBox="0 0 1200 72" aria-hidden="true">
    <polygon points="0,6 1020,6 1070,72 0,72" fill="var(--lime)"/>
    <polygon points="1020,6 1050,0 1110,72 1070,72" fill="var(--lime-dark)"/>
    <polygon points="1050,0 1200,0 1200,72 1110,72" fill="var(--lime)"/>
  </svg>

  <span class="footer-url">www.lumotex.com</span>
  <span class="page-number">Page : 01</span>
</main>
</body>
</html>
```